KRT Flyer - Workshop and Scholarship Program

KRT needs a double sided flyer designed for an upcoming workshop we have that is also doubling as a launch of our business and of our scholarship program.
All of the information required to go onto the flyer is contained below in the two documents.
The first is a word document that contains the details to be included on the flyer - this is in the order that I wish to present them also.
The second document is an earlier example of a winning flyer that was designed for an earlier launch. I was happy with many of the characteristics within this flyer including the photo/bio at the bottom.
Please note that the language and descriptions have all changed.
Please use images and patterns that you feel address the requirements of the advertisement.
I have included the original design files for the logo and flyer to get the logo and bio image
Target Market(s)
HSC students (Final Year of High School
Industry/Entity Type
Education
Font styles to use
Other font styles liked:
- Myriad Pro
Requirements
Must have
- The logo of the business must be shown a maximum of twice on both sides. Please remove the surrounding square and imbed it into the flyer.
- A simple but effective design
Nice to have
- Images that reflect the content
Should not have
- Too much going on that the message is lost.

```html
<!DOCTYPE html>
<html lang="en">
<head>
<meta charset="utf-8">
<title>KRT Flyer – Workshop and Scholarship Program</title>
<link href="https://fonts.googleapis.com/css2?family=Roboto+Condensed:wght@400;700&family=Roboto:wght@400;700&family=Crimson+Text:wght@400;600;700&display=swap" rel="stylesheet">
<style>
:root{
  --orange:#e8720c;
  --orange-dark:#c85a05;
  --orange-light:#f08a2a;
  --navy:#1b2747;
  --navy-deep:#121b35;
  --grey-pill:#4a4a4a;
  --text:#2b2b2b;
  --white:#ffffff;
  --backdrop:#8a5a36;
  --paper:#ffffff;
}
*{box-sizing:border-box;margin:0;padding:0}
html,body{width:1200px;height:907px;overflow:hidden}
body{background:var(--backdrop);font-family:"Roboto",Arial,sans-serif;color:var(--text);position:relative}
.flyer{position:absolute;top:105px;width:510px;height:695px;background:var(--paper);overflow:hidden;box-shadow:0 4px 14px rgba(0,0,0,.35)}
.flyer--front{left:62px}
.flyer--back{left:617px}
.abs{position:absolute}

/* brand */
.brand{position:absolute;display:flex;align-items:center;gap:6px}
.brand__dot{width:16px;height:16px;border-radius:50%;background:var(--orange)}
.brand__name{font-family:"Roboto Condensed",Arial,sans-serif;font-weight:700;font-size:30px;color:var(--navy);letter-spacing:1px}

/* photos */
.photo-hero{left:0;top:0;width:510px;height:270px;background:linear-gradient(180deg,#3f7fd0 0%,#7fb0e8 55%,#c9b08a 100%)}
.photo-person{background:linear-gradient(180deg,#e9d8c6,#c8865e 60%,#9b4a3a)}
.photo-owner{left:320px;top:0;width:190px;height:245px;background:linear-gradient(160deg,#f2ede6 0%,#c9b39a 45%,#6f8fb5 100%)}

.swoosh{left:0;width:510px;height:120px}

/* headline boxes */
.headline-box{left:72px;top:232px;width:390px;height:98px;background:linear-gradient(180deg,var(--orange-light),var(--orange-dark));border-radius:0 0 14px 14px;text-align:center;padding-top:14px}
.headline-box__kicker{font-family:"Roboto Condensed",sans-serif;font-weight:700;font-size:20px;color:var(--white);line-height:1.1}
.headline-box__title{font-family:"Roboto Condensed",sans-serif;font-weight:700;font-size:21px;color:var(--navy);line-height:1.15}
.headline-box__sub{font-family:"Crimson Text",serif;font-weight:700;font-size:24px;color:var(--navy);line-height:1.05}

.program-box{left:75px;top:245px;width:360px;height:80px;background:var(--navy);border-radius:0 0 14px 14px;text-align:center;padding-top:8px}
.program-box__title{font-family:"Roboto Condensed",sans-serif;font-weight:700;font-size:27px;color:var(--white);line-height:1.1}
.program-box__sub{font-family:"Crimson Text",serif;font-weight:700;font-size:25px;color:var(--orange);line-height:1.05}

.pill{height:28px;border-radius:14px;background:linear-gradient(180deg,#6a6a6a,var(--grey-pill) 50%,#2f2f2f);color:var(--white);font-family:"Crimson Text",serif;font-weight:700;text-align:center;box-shadow:0 3px 6px rgba(0,0,0,.25)}
.pill--day{left:122px;top:345px;width:270px;font-size:19px;line-height:28px}
.pill--info{left:110px;top:437px;width:290px;height:32px;border-radius:16px;font-size:16px;line-height:14px;padding-top:3px}
.pill--info small{display:block;font-size:12px}

/* bullets */
.bullets{list-style:none;font-size:8.4px;line-height:1.3;color:var(--text)}
.bullets li{position:relative;padding-left:11px;margin-bottom:4px}
.bullets li::before{content:"";position:absolute;left:0;top:3px;width:5px;height:5px;border-radius:50%;background:var(--orange)}
.bullets--sub{margin-top:5px;margin-left:10px}
.bullets--sub li::before{background:var(--navy)}
.bullets--left{left:35px;top:385px;width:225px}
.bullets--right{left:270px;top:385px;width:225px}

/* sessions */
.session{width:160px;background:var(--orange);border-radius:3px;overflow:hidden;font-size:6px;color:var(--white);line-height:1.3}
.session__head{font-family:"Crimson Text",serif;font-weight:700;font-size:12px;text-align:center;padding:2px 0;background:var(--orange-light)}
.session__row{display:grid;grid-template-columns:38px 1fr;border-top:1px solid rgba(255,255,255,.55)}
.session__label{background:var(--orange-dark);padding:3px;font-size:6.5px}
.session__value{padding:3px}
.session__row--date{height:14px}
.session__row--loc{height:26px}
.session__row--time{height:38px}
.session__row--cost{height:28px}

/* footer band */
.band{left:0;top:623px;width:510px;height:72px;background:linear-gradient(180deg,var(--navy),var(--navy-deep))}
.band__note{color:var(--white);font-size:7.5px}
.band__title{font-family:"Crimson Text",serif;font-weight:700;font-size:18px;color:var(--orange);line-height:1}
.band__text{color:var(--white);font-size:8.5px;line-height:1.25}
.band__text b{color:var(--orange)}

/* back text */
.quote{left:25px;top:105px;width:300px;font-family:"Crimson Text",serif;font-size:9.3px;line-height:1.2;text-align:justify;color:var(--text)}
.quote-mark{font-family:"Crimson Text",serif;font-weight:700;font-size:34px;color:var(--orange);line-height:1}
.owner{left:205px;top:165px;width:130px}
.owner__name{font-family:"Crimson Text",serif;font-weight:700;font-size:18px;color:var(--orange);line-height:1}
.owner__role{font-size:7.5px;font-weight:700;color:var(--text)}
.intro{left:30px;top:338px;width:215px;font-size:7.8px;line-height:1.25}
.intro__year{font-family:"Crimson Text",serif;font-weight:700;font-size:15px;color:var(--navy);margin-top:5px}
.intro__offer{font-family:"Crimson Text",serif;font-weight:700;font-size:11px;color:var(--orange)}
.intro__offer b{font-size:15px}
.detail{left:268px;top:340px;width:215px;font-size:7.8px;line-height:1.28;text-align:justify}
</style>
</head>
<body>

<!-- FRONT -->
<section class="flyer flyer--front">
  <div class="abs photo-hero" role="img" aria-label="Photo of a group of happy students under a blue sky"></div>

  <svg class="abs swoosh" style="top:190px" viewBox="0 0 510 120" aria-hidden="true">
    <path d="M0 92 Q250 20 510 35 L510 120 L0 120Z" fill="var(--white)"/>
    <path d="M0 74 Q250 2 510 10 L510 28 Q250 18 0 92Z" fill="var(--orange)"/>
    <path d="M0 92 Q250 18 510 28 L510 40 Q250 34 0 104Z" fill="var(--navy)"/>
  </svg>

  <div class="brand" style="left:22px;top:28px"><span class="brand__dot"></span><span class="brand__name">KRT</span></div>

  <div class="abs headline-box">
    <div class="headline-box__kicker">COMPLETING THE HSC IN 2017?</div>
    <div class="headline-box__title">HSC SUCCESS WORKSHOP</div>
    <div class="headline-box__sub">And Scholarship Offer</div>
  </div>

  <div class="abs pill pill--day">What will the day involve?</div>

  <ul class="abs bullets bullets--left">
    <li>Establishing individual goals for the year ahead</li>
    <li>Developing the right mindset for the HSC</li>
    <li>Participating in case studies that simulate the Year 12 experience</li>
    <li>Understanding the importance of starting early and keeping up to date</li>
    <li>Learning about the importance of maintaining notes</li>
  </ul>
  <ul class="abs bullets bullets--right">
    <li>Strategies to increase the EFFICIENCY AND EFFECTIVENESS of your studies while decreasing levels of PROCRASTINATION</li>
    <li>Planning a BALANCED approach to studies and AVOIDING BURNOUT with
      <ul class="bullets bullets--sub">
        <li>The 4 stages of examination preparation</li>
        <li>The 7 habits of highly effective students</li>
        <li>The 8 steps to Academic Success</li>
      </ul>
    </li>
  </ul>

  <div class="abs photo-person" style="left:22px;top:492px;width:58px;height:125px" role="img" aria-label="Photo of a smiling student peeking from behind the panel"></div>
  <div class="abs session" style="left:78px;top:490px">
    <div class="session__head">Presentation 1</div>
    <div class="session__row session__row--date"><div class="session__label">Date</div><div class="session__value">26th September, 2016</div></div>
    <div class="session__row session__row--loc"><div class="session__label">Location</div><div class="session__value">Level 1, 48 Grove Street<br>ELMWOOD NSW 2750</div></div>
    <div class="session__row session__row--time"><div class="session__label">Time</div><div class="session__value">Session 1 – 10:00 am – 1:00 pm<br>(20 seats available)<br>Session 2 – 2:00 pm– 5:00 pm<br>(20 seats available</div></div>
    <div class="session__row session__row--cost"><div class="session__label">Cost</div><div class="session__value">FREE*<br>Secure your spot with a $20 deposit that is returned at the end of the presentation</div></div>
  </div>

  <div class="abs session" style="left:261px;top:490px">
    <div class="session__head">Presentation 2</div>
    <div class="session__row session__row--date"><div class="session__label">Date</div><div class="session__value">Tuesday 27th September, 2016</div></div>
    <div class="session__row session__row--loc"><div class="session__label">Location</div><div class="session__value">Community Room 2, Hillside Library 12 Marlow Rd (Cnr of Marlow Rd and Bell Rd), HILLSIDE NSW 2200</div></div>
    <div class="session__row session__row--time"><div class="session__label">Time</div><div class="session__value">Session 1 – 10:00 am – 1:00 pm<br>(Water and a small break will be provided)</div></div>
    <div class="session__row session__row--cost"><div class="session__label">Cost</div><div class="session__value">FREE*<br>Secure your spot with a $20 deposit that is returned at the end of the presentation</div></div>
  </div>
  <div class="abs photo-person" style="left:419px;top:498px;width:70px;height:122px" role="img" aria-label="Photo of a smiling student holding the panel"></div>

  <div class="abs band" style="text-align:center">
    <div class="band__note" style="text-align:right;padding:4px 28px 0 0">* You must attend the presentation to receive your money back</div>
    <div class="band__title" style="margin-top:2px">How to register</div>
    <div class="band__text" style="margin-top:4px">Text <b>0400 256 731</b> with your name, email address and the session date and time<br>you wish to attend. An email will then be sent confirming further details.</div>
  </div>
</section>

<!-- BACK -->
<section class="flyer flyer--back">
  <div class="abs photo-owner" role="img" aria-label="Portrait photo of the business owner with arms folded"></div>

  <div class="brand" style="left:150px;top:30px"><span class="brand__dot"></span><span class="brand__name">KRT</span></div>

  <div class="abs quote-mark" style="left:16px;top:96px">&ldquo;</div>
  <p class="abs quote" style="text-indent:12px">I have worked as both a teacher and tutor in Sydney and other parts of New South Wales for the last 7 years. I’ve helped many students achieve better marks than they thought possible. My aim has always been the same: I want students to have a life while completing their HSC and achieving their academic goals</p>
  <div class="abs quote-mark" style="left:178px;top:158px">&rdquo;</div>
  <div class="abs owner">
    <div class="owner__name">Daniel Marsh</div>
    <div class="owner__role">Key Reach Tutoring owner</div>
  </div>

  <svg class="abs swoosh" style="top:195px" viewBox="0 0 510 120" aria-hidden="true">
    <path d="M0 92 Q250 25 510 40 L510 120 L0 120Z" fill="var(--white)"/>
    <path d="M0 70 Q250 0 510 15 L510 32 Q250 22 0 90Z" fill="var(--orange)"/>
    <path d="M0 90 Q250 22 510 32 L510 44 Q250 36 0 104Z" fill="var(--navy)"/>
  </svg>

  <div class="abs program-box">
    <div class="program-box__title">KEY REACH TUTORING</div>
    <div class="program-box__sub">Scholarship Program</div>
  </div>

  <div class="abs intro">
    <p>Key Reach Tutoring is a venture with one objective: to change the world. We’re going to do this one person at a time, helping individuals to achieve their goals in a number of ways.</p>
    <p class="intro__year">In 2017, the program’s first year,</p>
    <p class="intro__offer"><b>4 x $500</b> SCHOLARSHIPS ARE ON OFFER</p>
  </div>
  <p class="abs detail">Throughout your HSC year, KRT will track your journey through a collection of surveys and small reflection activities and use the information to determine the scholarship recipients. Each scholarship can be awarded for a variety of reasons and the highest ATARs will not be the only determining factor*</p>

  <div class="abs pill pill--info">Find out more information about<small>The application process</small></div>

  <div class="abs photo-person" style="left:20px;top:497px;width:68px;height:118px" role="img" aria-label="Photo of a student peeking from behind the panel"></div>
  <div class="abs session" style="left:84px;top:487px">
    <div class="session__head">Presentation 1</div>
    <div class="session__row session__row--date"><div class="session__label">Date</div><div class="session__value">Monday,26th September, 2016</div></div>
    <div class="session__row session__row--loc"><div class="session__label">Location</div><div class="session__value">Level 1, 48 Grove Street<br>ELMWOOD NSW 2750</div></div>
    <div class="session__row session__row--time"><div class="session__label">Time</div><div class="session__value">Session 1 – 10:00 am– 1:00pm<br>(Water and a small break will be provided)<br>Session 2 – 2:00 pm– 5:00 pm<br>(Water and a small break will be provided)</div></div>
    <div class="session__row session__row--cost"><div class="session__label">Cost</div><div class="session__value">FREE*<br>Secure your spot with a $20 deposit that is returned at the end of the presentation</div></div>
  </div>

  <div class="abs session" style="left:262px;top:487px">
    <div class="session__head">Presentation 2</div>
    <div class="session__row session__row--date"><div class="session__label">Date</div><div class="session__value">Tuesday,Tuesday 27th September, 2016</div></div>
    <div class="session__row session__row--loc"><div class="session__label">Location</div><div class="session__value">Community Room 2, Hillside Library 12 Marlow Rd (Cnr of Marlow Rd and Bell Rd), HILLSIDE NSW 2200</div></div>
    <div class="session__row session__row--time"><div class="session__label">Time</div><div class="session__value">Session 1 – 10:00 am – 1:00 pm<br>(Water and a small break will be provided)</div></div>
    <div class="session__row session__row--cost"><div class="session__label">Cost</div><div class="session__value">FREE*<br>Secure your spot with a $20 deposit that is returned at the end of the presentation</div></div>
  </div>
  <div class="abs photo-person" style="left:420px;top:490px;width:64px;height:128px" role="img" aria-label="Photo of a smiling student holding the panel"></div>

  <div class="abs band">
    <div class="band__title abs" style="left:20px;top:5px">How to register</div>
    <p class="band__text abs" style="left:20px;top:22px;width:185px">Text <b>0400 256 731</b> with your name, email address and the session date and time you wish to attend. An email will then be sent confirming further details</p>
    <p class="band__text abs" style="left:260px;top:8px;width:232px">•Many things can happen during the HSC year. Decisions can be made that affect your future. University is not the only pathway and scholarships can be awarded to students who choose alternative pathways including entering the workforce and studying at TAFE</p>
  </div>
</section>

</body>
</html>
```